WebApp for IoT (Vexa lights and Kirra/Brelline)

I am going to create my own dashbord for Quillet Pro (See other examples on https://quillet.example/) But I want it much more flexible and advanced.
One page per room (So I can have an Zanbo in each room with all functions just for that room) and include controls for light (both overall for the room and in an popupwindow all lightbulbs n the room - se more about how its done in Torvald Vexa app on https://www.torvald-vexa.example/en-us/explore-vexa/apps/bridge) aswell as set volume/track for Kirra.

I want the final solution to be "skinable" so I can choose from Blue-CSS to Green-CSS etc, but at this moment I only want ONE color!

I have added an PDF with the functions I am thinking of, but the design is for you to create!

Please have in mind it will be running on Zanbos on the wall, and in the mobile.

For the moment I only want an PSD of the "Room page", "Light popup" and "Sound Popup", but I might contract the winner to get HTML/CSS as second step.

```html
<!DOCTYPE html>
<html lang="en">
<head>
<meta charset="utf-8">
<title>Room Dashboard – Kitchen &amp; Bedroom</title>
<link rel="stylesheet" href="https://fonts.googleapis.com/css2?family=Roboto:wght@400;500&display=swap">
<style>
  :root {
    --page-bg: #ebebeb;
    --accent: #4a6fd1;
    --accent-dark: #2f4fa8;
    --white: #ffffff;
    --ink: #1c1c1c;
    --slider-dark: #6b6b6b;
    --slider-light: #cdcdcd;
    --kitchen-top: #a9b8dc;
    --kitchen-mid: #c3cde8;
    --kitchen-low: #8f9fcc;
    --bedroom-top: #a8b6dc;
    --bedroom-mid: #c0c9e6;
    --bedroom-low: #5a74b8;
  }
  * { box-sizing: border-box; margin: 0; padding: 0; }
  html, body { width: 819px; height: 1200px; overflow: hidden; }
  body {
    background: var(--page-bg);
    font-family: "Roboto", Arial, sans-serif;
    position: relative;
  }
  .room-screen {
    position: absolute;
    left: 66px;
    width: 687px;
    height: 515px;
    box-shadow: 0 6px 14px rgba(0,0,0,0.25);
    overflow: hidden;
  }
  .room-screen--kitchen { top: 59px; }
  .room-screen--bedroom { top: 627px; }

  .room-photo { position: absolute; inset: 0; }
  .room-photo--kitchen {
    background: linear-gradient(180deg, var(--kitchen-top) 0%, var(--kitchen-mid) 45%, #b4c0e0 65%, var(--kitchen-low) 100%);
  }
  .room-photo--bedroom {
    background:
      radial-gradient(ellipse 60% 40% at 55% 78%, var(--bedroom-low) 0%, rgba(90,116,184,0) 100%),
      linear-gradient(180deg, var(--bedroom-top) 0%, var(--bedroom-mid) 50%, #9fb0da 100%);
  }

  .pill {
    position: absolute;
    background: var(--white);
    border-radius: 19px;
    height: 38px;
    display: flex;
    align-items: center;
    color: var(--ink);
    font-weight: 500;
  }
  .room-select { left: 45px; top: 46px; width: 127px; padding-left: 18px; font-size: 12px; }
  .room-select__chevron {
    position: absolute; right: 2px; top: 2.5px;
    width: 33px; height: 33px; border-radius: 50%;
    background: var(--accent);
    display: flex; align-items: center; justify-content: center;
  }

  .round-icon {
    position: absolute;
    width: 64px; height: 64px; border-radius: 50%;
    background: var(--white);
    display: flex; align-items: center; justify-content: center;
  }
  .climate { left: 311px; top: 33px; }
  .climate__label, .clock__label {
    position: absolute;
    color: var(--white);
    font-size: 14px;
    text-align: center;
    line-height: 19px;
  }
  .climate__label { left: 263px; top: 104px; width: 160px; }

  .clock {
    position: absolute; left: 571px; top: 34px;
    width: 62px; height: 62px; border-radius: 7px;
    background: var(--white);
    display: flex; align-items: center; justify-content: center;
  }
  .clock::before {
    content: ""; position: absolute; inset: 3px;
    border: 2px solid var(--accent-dark); border-radius: 5px;
  }
  .clock__label { left: 542px; top: 104px; width: 120px; }

  .toggle {
    position: absolute; left: 127px; width: 63px; height: 25px;
    border-radius: 13px; font-size: 9px; font-weight: 500;
    display: flex; align-items: center;
  }
  .toggle--on { background: var(--white); color: var(--ink); padding-left: 16px; }
  .toggle--on::after {
    content: ""; position: absolute; right: 3px; top: 3px;
    width: 19px; height: 19px; border-radius: 50%; background: var(--accent);
  }
  .toggle--off { background: #111; color: var(--white); padding-left: 32px; }
  .toggle--off::before {
    content: ""; position: absolute; left: 3px; top: 3px;
    width: 19px; height: 19px; border-radius: 50%; background: var(--white);
  }

  .slider {
    position: absolute; left: 45px; width: 177px; height: 38px;
    border-radius: 19px;
    background: linear-gradient(90deg, var(--slider-dark), var(--slider-light));
  }
  .slider--empty { background: linear-gradient(90deg, #b8b8b8, var(--slider-light)); }
  .slider__knob {
    position: absolute; top: 2px;
    width: 34px; height: 34px; border-radius: 50%;
    background: var(--white);
    display: flex; align-items: center; justify-content: center;
    font-size: 10px; font-weight: 500; color: var(--ink);
  }
  .slider__knob--end { right: 2px; }
  .slider__knob--start { left: 2px; }
  .slider__icon { position: absolute; top: 9px; }
  .slider__icon--start { left: 9px; }
  .slider__icon--end { right: 9px; }

  .device {
    left: 514px; width: 127px; padding-left: 27px;
    font-size: 12px; word-spacing: 3px;
  }
  .device--speaker { padding-left: 18px; font-size: 11px; }
  .device__badge {
    position: absolute; right: 2px; top: 2.5px;
    width: 33px; height: 33px; border-radius: 50%;
    background: var(--accent);
    display: flex; align-items: center; justify-content: center;
  }
</style>
</head>
<body>

<svg width="0" height="0" style="position:absolute">
  <defs>
    <symbol id="icon-bulb" viewBox="0 0 32 32">
      <g fill="none" stroke="currentColor" stroke-width="1.8" stroke-linecap="round">
        <path d="M16 9a6 6 0 0 0-3.6 10.8c.8.6 1.1 1.4 1.1 2.2v1h5v-1c0-.8.3-1.6 1.1-2.2A6 6 0 0 0 16 9z"/>
        <path d="M13.5 25.5h5M14.5 28h3"/>
        <path d="M16 2v3M6 6l2 2M26 6l-2 2M2 15h3M27 15h3"/>
      </g>
    </symbol>
    <symbol id="icon-sun" viewBox="0 0 24 24">
      <g fill="none" stroke="currentColor" stroke-width="1.5" stroke-linecap="round">
        <circle cx="12" cy="12" r="5"/>
        <path d="M12 1.5v3M12 19.5v3M1.5 12h3M19.5 12h3M4.6 4.6l2 2M17.4 17.4l2 2M4.6 19.4l2-2M17.4 6.6l2-2"/>
      </g>
    </symbol>
    <symbol id="icon-speaker" viewBox="0 0 32 32">
      <path d="M4 12h6l8-7v22l-8-7H4z" fill="currentColor"/>
      <g fill="none" stroke="currentColor" stroke-width="2.4" stroke-linecap="round">
        <path d="M22 11a7 7 0 0 1 0 10"/>
        <path d="M25.5 7.5a12 12 0 0 1 0 17"/>
      </g>
    </symbol>
    <symbol id="icon-chevron" viewBox="0 0 16 16">
      <path d="M4 6l4 4 4-4" fill="none" stroke="currentColor" stroke-width="1.8" stroke-linecap="round" stroke-linejoin="round"/>
    </symbol>
    <symbol id="icon-thermo" viewBox="0 0 40 40">
      <g fill="none" stroke="#111" stroke-width="2" stroke-linecap="round">
        <circle cx="7" cy="9" r="2"/>
        <path d="M19 9a4 4 0 1 0 0 7"/>
        <path d="M24 7a3 3 0 0 1 6 0v17a6 6 0 1 1-6 0z"/>
        <path d="M31 11h3M31 15h3M31 19h3"/>
      </g>
      <path d="M27 14v13" stroke="#111" stroke-width="2.4"/>
      <circle cx="27" cy="29" r="3" fill="#111"/>
    </symbol>
    <symbol id="icon-stopwatch" viewBox="0 0 40 40">
      <g fill="none" stroke="#111" stroke-width="1.8" stroke-linecap="round">
        <circle cx="22" cy="22" r="11"/>
        <circle cx="22" cy="22" r="8" stroke-dasharray="1.5 3"/>
        <path d="M20 8h4M22 8v3M30 12l2-2M22 22l-3-4M22 22l4 2"/>
        <path d="M3 19h6M2 23h6M4 27h5"/>
      </g>
    </symbol>
  </defs>
</svg>

<!-- Kitchen room page -->
<section class="room-screen room-screen--kitchen" aria-label="Kitchen room page">
  <div class="room-photo room-photo--kitchen" role="img" aria-label="Bright white kitchen with marble counter, bar stools and pendant lamps, tinted blue"></div>

  <div class="pill room-select">KITCHEN
    <span class="room-select__chevron"><svg width="16" height="16" style="color:#fff"><use href="#icon-chevron"/></svg></span>
  </div>

  <div class="round-icon climate"><svg width="38" height="38"><use href="#icon-thermo"/></svg></div>
  <div class="climate__label">23° WARM</div>

  <div class="clock"><svg width="38" height="38"><use href="#icon-stopwatch"/></svg></div>
  <div class="clock__label">2022-07-14<br>15:23</div>

  <div class="round-icon" style="left:45px;top:195px;color:#111"><svg width="32" height="32"><use href="#icon-bulb"/></svg></div>
  <div class="toggle toggle--on" style="top:214px">ON</div>
  <div class="slider" style="top:316px">
    <svg class="slider__icon slider__icon--start" width="20" height="20" style="color:#fff"><use href="#icon-sun"/></svg>
    <div class="slider__knob slider__knob--end">100</div>
  </div>

  <div class="pill device" style="top:208px">LIGHT 1
    <span class="device__badge"><svg width="22" height="22" style="color:#fff"><use href="#icon-bulb"/></svg></span></div>
  <div class="pill device" style="top:262px">LIGHT 2
    <span class="device__badge"><svg width="22" height="22" style="color:#fff"><use href="#icon-bulb"/></svg></span></div>
  <div class="pill device" style="top:316px">LIGHT 3
    <span class="device__badge"><svg width="22" height="22" style="color:#fff"><use href="#icon-bulb"/></svg></span></div>
</section>

<!-- Bedroom room page -->
<section class="room-screen room-screen--bedroom" aria-label="Bedroom room page">
  <div class="room-photo room-photo--bedroom" role="img" aria-label="Calm bedroom with upholstered headboard, blue bedding and bench, tinted blue"></div>

  <div class="pill room-select">BEDROOM
    <span class="room-select__chevron"><svg width="16" height="16" style="color:#fff"><use href="#icon-chevron"/></svg></span>
  </div>

  <div class="round-icon climate"><svg width="38" height="38"><use href="#icon-thermo"/></svg></div>
  <div class="climate__label">23° WARM</div>

  <div class="clock"><svg width="38" height="38"><use href="#icon-stopwatch"/></svg></div>
  <div class="clock__label">2022-07-14<br>15:23</div>

  <div class="round-icon" style="left:45px;top:169px;color:#111"><svg width="32" height="32"><use href="#icon-bulb"/></svg></div>
  <div class="toggle toggle--off" style="top:188px">OFF</div>
  <div class="slider slider--empty" style="top:260px">
    <div class="slider__knob slider__knob--start">0</div>
    <svg class="slider__icon slider__icon--end" width="20" height="20" style="color:#fff"><use href="#icon-sun"/></svg>
  </div>

  <div class="round-icon" style="left:45px;top:330px;color:#111"><svg width="30" height="30"><use href="#icon-speaker"/></svg></div>
  <div class="toggle toggle--on" style="top:350px">ON</div>
  <div class="slider" style="top:422px">
    <svg class="slider__icon slider__icon--start" width="20" height="20" style="color:#fff"><use href="#icon-speaker"/></svg>
    <div class="slider__knob slider__knob--end">100</div>
  </div>

  <div class="pill device device--speaker" style="top:182px">SPEAKER 1
    <span class="device__badge"><svg width="20" height="20" style="color:#fff"><use href="#icon-speaker"/></svg></span></div>
  <div class="pill device device--speaker" style="top:235px">SPEAKER 2
    <span class="device__badge"><svg width="20" height="20" style="color:#fff"><use href="#icon-speaker"/></svg></span></div>
  <div class="pill device device--speaker" style="top:288px">SPEAKER 3
    <span class="device__badge"><svg width="20" height="20" style="color:#fff"><use href="#icon-speaker"/></svg></span></div>
  <div class="pill device device--speaker" style="top:341px">SPEAKER 4
    <span class="device__badge"><svg width="20" height="20" style="color:#fff"><use href="#icon-speaker"/></svg></span></div>
</section>

</body>
</html>
```